"Harbor Builders" is a residential building company and needs a new business card design and may re

We would like a redesign based on the existing logo, and would like to see a new font as well. We are bespoke home builders who build sustainable energy efficient homes.

Industry/Entity Type

Construction

Contact Information for Business Card

Business card size 40mm x 90mm

Colors

Designer to choose colors to be used in the design.

```html
<!DOCTYPE html>
<html lang="en">
<head>
<meta charset="utf-8">
<title>Harbor Builders – Business Card</title>
<link href="https://fonts.googleapis.com/css2?family=Open+Sans:wght@400;600;700&display=swap" rel="stylesheet">
<style>
  :root {
    --backdrop: #3a3430;
    --card: #141414;
    --card-edge: #1d1d1d;
    --ink: #f2f2f2;
    --muted: #9a9a9a;
    --accent: #a4c23a;
    --rule: #6a6a6a;
  }
  * { box-sizing: border-box; margin: 0; padding: 0; }
  html, body {
    width: 1200px; height: 864px; overflow: hidden;
    background: var(--backdrop);
    font-family: "Open Sans", Arial, sans-serif;
  }
  .canvas {
    width: 1200px; height: 864px;
    display: flex; flex-direction: column; align-items: center; justify-content: center;
    gap: 56px;
  }
  .card {
    position: relative;
    width: 720px; height: 320px;
    background: var(--card);
    border: 1px solid var(--card-edge);
    box-shadow: 0 14px 30px rgba(0,0,0,.45);
    color: var(--ink);
  }
  /* Front */
  .card--front { display: flex; flex-direction: column; align-items: center; justify-content: center; gap: 26px; }
  .brand { display: flex; align-items: center; gap: 14px; }
  .brand__square { width: 26px; height: 26px; background: var(--accent); }
  .brand__name { font-weight: 700; color: var(--ink); letter-spacing: .5px; }
  .card--front .brand__name { font-size: 46px; }
  .card--front .brand__square { width: 40px; height: 40px; }
  .front__web { font-size: 15px; letter-spacing: 3px; color: var(--muted); }
  /* Back */
  .back__rule { position: absolute; left: 40px; right: 40px; top: 150px; height: 1px; background: var(--rule); }
  .contact { position: absolute; left: 40px; top: 44px; font-size: 15px; line-height: 21px; }
  .contact__name { color: var(--accent); font-weight: 700; font-size: 17px; text-transform: uppercase; margin-bottom: 4px; }
  .contact__row { display: flex; align-items: center; gap: 8px; }
  .contact__row svg { width: 12px; height: 12px; flex: none; }
  .contact__row--plain { padding-left: 0; }
  .card--back .brand { position: absolute; right: 40px; top: 70px; }
  .card--back .brand__name { font-size: 32px; }
  .address { position: absolute; right: 40px; bottom: 40px; text-align: right; font-size: 16px; line-height: 23px; }
</style>
</head>
<body>
<main class="canvas">
  <section class="card card--front">
    <div class="brand">
      <span class="brand__square"></span>
      <span class="brand__name">Harbor Builders</span>
    </div>
    <p class="front__web">www.harborbuilders.com.au</p>
  </section>

  <section class="card card--back">
    <div class="contact">
      <p class="contact__name">Daniel Marsh</p>
      <p>Registration 40318</p>
      <p>ABN: 42 305 118 774</p>
      <p class="contact__row">
        <svg viewBox="0 0 12 12"><rect x="3" y="0.5" width="6" height="11" rx="1" fill="none" stroke="var(--accent)" stroke-width="1.5"/></svg>
        0400 555 018
      </p>
      <p class="contact__row">
        <svg viewBox="0 0 12 12"><rect x="0.5" y="2" width="11" height="8" fill="var(--accent)"/><path d="M0.5 2 L6 7 L11.5 2" fill="none" stroke="var(--card)" stroke-width="1"/></svg>
        daniel@harborbuilders.com.au
      </p>
      <p class="contact__row">
        <svg viewBox="0 0 12 12"><circle cx="6" cy="6" r="5.5" fill="var(--accent)"/><path d="M0.5 6 H11.5 M6 0.5 V11.5" stroke="var(--card)" stroke-width="1"/></svg>
        www.harborbuilders.com.au
      </p>
    </div>

    <div class="brand">
      <span class="brand__square"></span>
      <span class="brand__name">Harbor Builders</span>
    </div>

    <div class="back__rule"></div>

    <address class="address" style="font-style:normal">
      Harbor Builders Pty Ltd<br>
      PO Box 2187<br>
      Northgate<br>
      LPO Riverton WA 6120
    </address>
  </section>
</main>
</body>
</html>
```